Healthcare technology firm needs business card layout. Logo provided.

We need a business card design for a new healthcare technology company called BelnaVix.net. The logo is already done so that will be used in the design. We assist patients and their families manage their personal health finances. Our initial product is our web site membership that includes educational content on your health benefits, tools, and downloadable forms.

We would like to see designs that use our existing logo or extend the logo in a creative way. Should be very consumer friendly.

Industry/Entity Type

Healthcare

```html
<!DOCTYPE html>
<html lang="en">
<head>
<meta charset="utf-8">
<title>BelnaVix Business Card</title>
<link rel="stylesheet" href="https://fonts.googleapis.com/css2?family=Questrial&family=Mulish:ital,wght@1,700&display=swap">
<style>
  :root {
    --stage: #e9edf0;
    --blue-light: #2a98dc;
    --blue-deep: #0b4f9f;
    --brand-blue: #1565b5;
    --brand-green: #3fb34f;
    --white: #ffffff;
    --ink: #3a3a3a;
    --card-shadow: 0 10px 30px rgba(20, 40, 60, 0.18);
  }
  * { box-sizing: border-box; margin: 0; padding: 0; }
  html, body {
    width: 1200px;
    height: 960px;
    overflow: hidden;
    background: var(--stage);
  }
  .stage {
    width: 1200px;
    height: 960px;
    display: flex;
    flex-direction: column;
    align-items: center;
    justify-content: center;
    gap: 60px;
  }
  .card {
    width: 700px;
    height: 400px;
    position: relative;
    box-shadow: var(--card-shadow);
    overflow: hidden;
  }

  /* Front */
  .card-front {
    background: linear-gradient(180deg, var(--blue-light) 0%, var(--blue-deep) 100%);
  }
  .front-logo {
    position: absolute;
    left: 0; right: 0;
    top: 120px;
    display: flex;
    justify-content: center;
    align-items: center;
    gap: 18px;
    font-family: "Questrial", sans-serif;
    font-size: 92px;
    letter-spacing: 2px;
    color: var(--white);
    line-height: 1;
  }
  .logo-dot {
    width: 26px;
    height: 26px;
    border-radius: 50%;
    background: var(--brand-green);
    flex: none;
  }
  .tagline-row {
    position: absolute;
    left: 0; right: 0;
    top: 282px;
    display: flex;
    align-items: center;
    gap: 14px;
  }
  .tagline-rule {
    flex: 1;
    height: 2px;
    background: var(--white);
  }
  .tagline-rule.short { flex: 0 0 130px; }
  .tagline {
    font-family: "Mulish", sans-serif;
    font-style: italic;
    font-weight: 700;
    font-size: 26px;
    color: var(--white);
    white-space: nowrap;
  }

  /* Back */
  .card-back {
    background: var(--white);
    display: flex;
    align-items: center;
  }
  .back-logo {
    flex: 0 0 370px;
    display: flex;
    align-items: center;
    justify-content: center;
    gap: 12px;
    font-family: "Questrial", sans-serif;
    font-size: 52px;
    letter-spacing: 1px;
    color: var(--brand-blue);
    line-height: 1;
  }
  .back-logo .logo-dot { width: 16px; height: 16px; }
  .contact {
    flex: 1;
    padding-right: 40px;
    font-family: "Questrial", sans-serif;
    color: var(--ink);
  }
  .contact-name { font-size: 24px; line-height: 1.15; }
  .contact-title { font-size: 24px; line-height: 1.15; }
  .contact-row {
    border-top: 3px dotted var(--brand-green);
    padding-top: 8px;
    margin-top: 8px;
    font-size: 18px;
    line-height: 1.35;
  }
</style>
</head>
<body>
  <main class="stage">
    <section class="card card-front" aria-label="Business card front">
      <div class="front-logo">
        <span class="brand-name">BelnaVix</span>
        <span class="logo-dot"></span>
      </div>
      <div class="tagline-row">
        <span class="tagline-rule short"></span>
        <span class="tagline">Helping your health budget thrive</span>
        <span class="tagline-rule"></span>
      </div>
    </section>

    <section class="card card-back" aria-label="Business card back">
      <div class="back-logo">
        <span class="brand-name">BelnaVix</span>
        <span class="logo-dot"></span>
      </div>
      <div class="contact">
        <p class="contact-name">Marion T. Hale</p>
        <p class="contact-title">CEO</p>
        <p class="contact-row">M: 555-014-2276</p>
        <p class="contact-row">www.belnavix.net</p>
        <p class="contact-row">Oak Harbor<br>Cedar Falls<br>Pine Ridge, Lakeview</p>
      </div>
    </section>
  </main>
</body>
</html>
```